Managed IT services business card design

We haven't needed a business card since the founding of the business in 2005. All our clients have been coming through word of mouth. And lately more and more existing clients are requesting for our business cards to pass on to their contacts in recommending us.
So we needing a business card design. We use various innovative solutions and methodologies to provide IT services to small businesses in managing their IT systems. Our role is the same as an in-house, full-time IT Manager for our clients, but outsourced. So we take care of all our clients' IT needs, just as an IT Manager would be expected to perform.
We have a holding website, which we're happy to leave for now. If we can use the same logo would be great - www.lumadesk.com.au
Preferred colours are shades of are white, grey and black.
We pride our business with the following traits: proactive, good service, prompt response, trustworthy.
Target Market(s)
Small businesses of any industry
Industry/Entity Type
Business

```html
<!DOCTYPE html>
<html lang="en">
<head>
<meta charset="utf-8">
<title>Lumadesk – Business Card</title>
<link rel="stylesheet" href="https://fonts.googleapis.com/css2?family=Open+Sans:wght@400;600&display=swap">
<style>
  :root {
    --stage: #e4e5e6;
    --card-white: #ffffff;
    --card-grey: #5b6064;
    --ink: #1c1c1c;
    --swoosh: #111111;
    --light-text: #ffffff;
    --shadow: rgba(0, 0, 0, 0.18);
  }
  * { margin: 0; padding: 0; box-sizing: border-box; }
  html, body {
    width: 1200px;
    height: 680px;
    overflow: hidden;
    background: var(--stage);
    font-family: "Open Sans", sans-serif;
  }
  .stage {
    position: relative;
    width: 1200px;
    height: 680px;
  }
  .card {
    position: absolute;
    top: 190px;
    width: 525px;
    height: 300px;
    border-radius: 18px;
    overflow: hidden;
    box-shadow: 0 6px 18px var(--shadow);
  }
  .card--front { left: 45px; background: var(--card-white); }
  .card--back  { left: 630px; background: var(--card-grey); }

  .swoosh { position: absolute; inset: 0; }

  .wordmark {
    position: absolute;
    display: flex;
    align-items: center;
    gap: 14px;
    font-weight: 400;
    letter-spacing: 0.28em;
    white-space: nowrap;
  }
  .wordmark__square {
    width: 10px;
    height: 10px;
    background: currentColor;
  }
  .card--front .wordmark {
    left: 36px;
    top: 124px;
    font-size: 30px;
    color: var(--ink);
  }

  .contact {
    position: absolute;
    left: 305px;
    top: 22px;
    color: var(--ink);
    font-size: 12.5px;
    line-height: 1.3;
  }
  .contact__name { font-size: 16px; letter-spacing: 0.02em; }
  .contact__role { font-size: 11.5px; margin-bottom: 10px; }
  .contact__address { margin-bottom: 4px; padding-left: 22px; }
  .contact__line {
    display: flex;
    align-items: center;
    gap: 8px;
  }
  .contact__line svg { width: 13px; height: 13px; flex: none; }

  .web {
    position: absolute;
    color: var(--light-text);
    font-size: 13px;
    letter-spacing: 0.35em;
    white-space: nowrap;
  }
  .card--front .web { right: 36px; bottom: 18px; }

  .card--back .wordmark {
    left: 50%;
    top: 104px;
    transform: translateX(-50%);
    font-size: 48px;
    letter-spacing: 0.32em;
    color: var(--light-text);
  }
  .card--back .web {
    left: 50%;
    bottom: 62px;
    transform: translateX(-50%);
  }
</style>
</head>
<body>
<main class="stage">

  <section class="card card--front" aria-label="Business card front">
    <svg class="swoosh" viewBox="0 0 525 300" preserveAspectRatio="none" aria-hidden="true">
      <path d="M0,300 V292 C170,274 370,232 525,206 V300 Z" fill="var(--card-grey)"/>
      <path d="M0,284 C170,264 370,214 525,188 V200 C370,226 170,272 0,289 Z" fill="var(--swoosh)"/>
    </svg>

    <div class="wordmark">
      <span>lumadesk</span>
      <span class="wordmark__square"></span>
    </div>

    <div class="contact">
      <p class="contact__name">Marcus Allard</p>
      <p class="contact__role">director</p>
      <p class="contact__address">418 Halden Park Rd<br>Corvale TX 78410</p>
      <p class="contact__line">
        <svg viewBox="0 0 16 16" aria-label="Phone"><path d="M4 1.5 6 4.5 4.8 6c.8 1.8 2.2 3.3 4.1 4.2L10.5 9l3 2-1 2.6c-5.6-.4-10-4.8-10.4-10.4Z" fill="none" stroke="currentColor" stroke-width="1.3"/></svg>
        512 330 4172
      </p>
      <p class="contact__line">
        <svg viewBox="0 0 16 16" aria-label="Fax"><rect x="4" y="2" width="8" height="5" fill="none" stroke="currentColor" stroke-width="1.2"/><rect x="1.5" y="7" width="13" height="7" rx="1" fill="currentColor"/></svg>
        512 330 4173
      </p>
      <p class="contact__line">
        <svg viewBox="0 0 16 16" aria-label="Email"><rect x="1.5" y="3.5" width="13" height="9" fill="currentColor"/><path d="M1.5 3.5 8 9l6.5-5.5" fill="none" stroke="#fff" stroke-width="1.2"/></svg>
        hello@lumadesk.com.au
      </p>
    </div>

    <p class="web">www.lumadesk.com.au</p>
  </section>

  <section class="card card--back" aria-label="Business card back">
    <div class="wordmark">
      <span>lumadesk</span>
      <span class="wordmark__square"></span>
    </div>
    <p class="web">www.lumadesk.com.au</p>
  </section>

</main>
</body>
</html>
```